Brenton's Insurance Servives, Inc.

Full Service Insurance Broker.
Senior Health Care, Life, Annuity, Auto and Home
Specializing in Medicare Supplements. No cost, No Obligation Consulting.

Target Market(s)

General Public and senior citizens

Industry/Entity Type

Insurance Broker

Font styles to use
Decorative
Script

```html
<!DOCTYPE html>
<html lang="en">
<head>
<meta charset="utf-8">
<title>Brenton's Insurance Servives, Inc. – Medicare Supplements Banner</title>
<link rel="stylesheet" href="https://fonts.googleapis.com/css2?family=Great+Vibes&family=Montserrat:wght@500;600;700;800&display=swap">
<style>
  :root{
    --page:#e6e6e6;
    --white:#ffffff;
    --brand-blue:#2f86c8;
    --script-blue:#2f7fc4;
    --ink:#2b2b2b;
    --navy:#1b2a6b;
    --navy-deep:#121c52;
    --sky:#3fa9f5;
    --photo-a:#e9ecea;
    --photo-b:#b9c6b8;
    --photo-c:#6f7f5e;
    --photo-d:#d9c3a8;
  }
  *{margin:0;padding:0;box-sizing:border-box}
  html,body{width:1200px;height:733px;overflow:hidden;background:var(--page)}
  .banner{position:absolute;left:0;top:67px;width:1200px;height:599px;background:var(--white);overflow:hidden;font-family:'Montserrat',sans-serif}
  .photo-area{position:absolute;left:470px;top:0;width:730px;height:599px;
    background:
      radial-gradient(ellipse 45% 55% at 70% 70%, var(--photo-d) 0%, transparent 70%),
      radial-gradient(ellipse 50% 50% at 35% 70%, #dfe6ee 0%, transparent 70%),
      linear-gradient(160deg, var(--photo-a) 0%, var(--photo-b) 45%, var(--photo-c) 100%);
    -webkit-mask-image:linear-gradient(90deg, transparent 0%, #000 30%);
            mask-image:linear-gradient(90deg, transparent 0%, #000 30%);}
  .brand{position:absolute;left:147px;top:28px;width:300px;display:flex;flex-direction:column;align-items:center;gap:8px}
  .brand-mark{width:34px;height:34px;border-radius:50%;background:var(--navy)}
  .brand-name{font-family:'Montserrat',sans-serif;font-weight:600;font-size:13px;color:var(--navy);white-space:nowrap}
  .headline-script{position:absolute;left:102px;top:102px;font-family:'Great Vibes',cursive;font-size:100px;color:var(--script-blue);line-height:1;white-space:nowrap}
  .headline{position:absolute;left:172px;top:190px;font-weight:700;font-size:35px;line-height:35px;color:var(--ink);white-space:nowrap}
  .headline-line{display:block}
  .headline-line--first{margin-left:20px}
  .headline-rule{position:absolute;left:228px;top:266px}
  .benefits{position:absolute;left:50px;top:312px;display:flex;gap:12px;font-size:24px;font-weight:500;color:var(--ink);align-items:center}
  .benefit{display:flex;align-items:center;gap:6px}
  .services{position:absolute;left:19px;top:357px;width:583px;height:150px;background:var(--brand-blue);border-radius:70px 70px 0 0;display:flex;justify-content:center;padding:14px 10px 0}
  .service{width:104px;text-align:center;color:var(--white);font-weight:600;font-size:15px;line-height:17px;display:flex;flex-direction:column;align-items:center;position:relative}
  .service + .service::before{content:"";position:absolute;left:0;top:20px;height:90px;border-left:1.5px solid rgba(255,255,255,.8)}
  .service-icon{width:80px;height:80px;border-radius:50%;background:var(--white);display:flex;align-items:center;justify-content:center;margin-bottom:10px}
  .call-bar{position:absolute;left:17px;top:503px;width:586px;height:50px;border-radius:25px;background:linear-gradient(180deg,var(--navy) 0%,var(--navy-deep) 100%);color:var(--white);font-weight:800;font-size:32px;display:flex;align-items:center;justify-content:center;gap:10px}
  .call-label{color:var(--sky)}
  .web{position:absolute;left:17px;top:561px;width:586px;text-align:center;font-size:25px;font-weight:600;letter-spacing:2px;color:var(--navy)}
  .web .accent{color:var(--sky)}
</style>
</head>
<body>
<main class="banner">
  <div class="photo-area" role="img" aria-label="Photo of a smiling senior woman with a caregiver resting hands on her shoulders"></div>

  <div class="brand">
    <span class="brand-mark"></span>
    <span class="brand-name">Brenton's Insurance Servives, Inc.</span>
  </div>

  <div class="headline-script">Specializing</div>
  <h1 class="headline"><span class="headline-line headline-line--first">in Medicare</span><span class="headline-line">Supplements.</span></h1>
  <svg class="headline-rule" width="146" height="24" viewBox="0 0 146 24"><path d="M2 22 Q60 2 144 4" fill="none" stroke="var(--ink)" stroke-width="2"/></svg>

  <div class="benefits">
    <span class="benefit"><svg width="34" height="30" viewBox="0 0 34 30"><circle cx="14" cy="16" r="12" fill="none" stroke="var(--brand-blue)" stroke-width="2.5"/><path d="M8 15 L14 21 L32 2" fill="none" stroke="var(--brand-blue)" stroke-width="3"/></svg>No cost,</span>
    <span class="benefit"><svg width="34" height="30" viewBox="0 0 34 30"><circle cx="14" cy="16" r="12" fill="none" stroke="var(--brand-blue)" stroke-width="2.5"/><path d="M8 15 L14 21 L32 2" fill="none" stroke="var(--brand-blue)" stroke-width="3"/></svg>No Obligation Consulting.</span>
  </div>

  <section class="services">
    <div class="service">
      <span class="service-icon"><svg width="50" height="50" viewBox="0 0 50 50" fill="none" stroke="var(--navy)" stroke-width="2.5"><path d="M10 6 v14 a10 10 0 0 0 20 0 v-14"/><path d="M20 30 v6 a8 8 0 0 0 16 0 v-4"/><circle cx="36" cy="27" r="5"/></svg></span>
      Senior<br>Health Care
    </div>
    <div class="service">
      <span class="service-icon"><svg width="50" height="50" viewBox="0 0 50 50" fill="none" stroke="var(--navy)" stroke-width="2.5"><path d="M25 24 C14 16 16 6 25 11 C34 6 36 16 25 24Z"/><path d="M22 15 h6 M25 12 v6"/><path d="M6 22 v12 l10 8 M44 22 v12 l-10 8"/><path d="M10 28 l8 6 M40 28 l-8 6"/></svg></span>
      Life
    </div>
    <div class="service">
      <span class="service-icon"><svg width="52" height="50" viewBox="0 0 52 50" fill="none" stroke="var(--navy)" stroke-width="2.5"><rect x="6" y="8" width="28" height="26" rx="2"/><path d="M6 15 h28 M12 5 v6 M28 5 v6 M11 20 h4 M18 20 h4 M25 20 h4 M11 26 h4 M18 26 h4"/><circle cx="37" cy="34" r="10" fill="var(--white)"/><path d="M40 30 h-5 a2 2 0 0 0 0 4 h4 a2 2 0 0 1 0 4 h-5 M37 28 v12"/></svg></span>
      Annuity
    </div>
    <div class="service">
      <span class="service-icon"><svg width="54" height="50" viewBox="0 0 54 50" fill="none" stroke="var(--navy)" stroke-width="2.5"><path d="M8 26 l6 -12 h26 l6 12 v12 h-38z"/><path d="M8 26 h38"/><circle cx="15" cy="32" r="2.5"/><circle cx="39" cy="32" r="2.5"/><path d="M21 31 h12 M11 38 v5 M43 38 v5"/></svg></span>
      Auto
    </div>
    <div class="service">
      <span class="service-icon"><svg width="52" height="50" viewBox="0 0 52 50" fill="none" stroke="var(--navy)" stroke-width="2.5"><path d="M4 22 L26 6 L48 22"/><path d="M10 18 v24 h32 v-24"/><rect x="22" y="30" width="8" height="12"/><rect x="13" y="24" width="6" height="6"/><rect x="33" y="24" width="6" height="6"/><path d="M6 42 h40"/></svg></span>
      Home
    </div>
  </section>

  <div class="call-bar"><span class="call-label">Call us:</span><span>555-014-2290 or 014-3</span></div>
  <div class="web"><span class="accent">www.</span>brentoninsservices<span class="accent">.com</span></div>
</main>
</body>
</html>
```